High impact classy folder for an HVAC and Electrical contractor

We need a folder designed. It needs to be high impact and classy with a rich look to it. We want to cement our branding via the use of the folder so the look will need to have impact with use of our logo and colors.

We want to pull the entire brand look and feel together with this folder. We are going to be making other marketing materials and this is the start of a much larger project. In the ideal situation the winning desginer will continue on with the rest of the projects because they will know how to apply the brand look.

We want to give our local company the feel of a national franchise. Wherein the brand is very prominent and is repeated over and over again.

Use of logo and color scheme will be important.

We like dark backgrounds because they really make the logo pop.

Target Market(s)

homeowners

Font styles to use
Serif

Requirements
Must have
• Logo prominent on the front
• Our Tag Line:
• The Best Way To Live In New Jersey Is With Harbel"
• On the inside pockets:
• Our Phone number: 973-555-0148
• A message to our customers:
• We want to thank you for choosing Harbel Tradeworks today
• Our name says it all, because for over 30 years we have prided ourselves on delivering the best service and exceeding our customers' expectations everyday. Whether you need something fixed, replaced or upgraded, no matter how large or small, the dedicated and experts at Harbel Tradeworks are here to take care of you. Delivering the right solution for you the first time- everytime - and ensuring you are always 100% satisfied. If for any reason you want to speak with us, please do not hesitate to call or email. Thank you again for choosing Harbel Tradeworks.
• On the rear: a graphic that says 24-7 service
• A list of other services we provide:
• Solar
• Generators
• Home Security
• Home Automation
• Home Inspection
• Energy Audits
• 1 Day Bathroom remodles
• Basement Waterproofing
• Garage Doors
• Home Theaters
Nice to have
• I added photos of a flyer and of a mobile website to give an idea of the color scheme as well

```html
<!DOCTYPE html>
<html lang="en">
<head>
<meta charset="utf-8">
<title>Harbel Tradeworks – Presentation Folder</title>
<link href="https://fonts.googleapis.com/css2?family=Montserrat:ital,wght@0,400;0,600;0,700;1,400;1,600&family=Roboto+Slab:wght@700&display=swap" rel="stylesheet">
<style>
  :root {
    --red-deep: #7e1419;
    --red: #9a1c22;
    --red-light: #b0323a;
    --cream: #fbf1cc;
    --cream-deep: #f2e3b2;
    --orange: #e98a3c;
    --orange-light: #f2a65a;
    --ink-cream: #f6e6c4;
    --bg: #d9d9d9;
  }
  * { box-sizing: border-box; margin: 0; padding: 0; }
  html, body { width: 842px; height: 1200px; overflow: hidden; background: var(--bg); }
  body { font-family: "Montserrat", sans-serif; position: relative; }

  .spread { position: absolute; left: 16px; width: 810px; height: 560px; display: flex; box-shadow: 0 6px 18px rgba(0,0,0,.18); }
  .spread--outside { top: 24px; }
  .spread--inside { top: 616px; }
  .panel { position: relative; width: 405px; height: 560px; overflow: hidden; }

  /* back cover */
  .back { background: radial-gradient(circle at 30% 20%, var(--red-light), var(--red) 45%, var(--red-deep)); color: var(--ink-cream); }
  .faint-name { position: absolute; left: 0; right: 0; text-align: center; font-family: "Montserrat", sans-serif; font-weight: 600; font-size: 46px; line-height: 1.05; letter-spacing: 1px; }
  .back .faint-name { top: 120px; color: rgba(0,0,0,.1); }
  .back-info { position: absolute; top: 290px; left: 40px; right: 40px; text-align: center; }
  .back-info p { font-size: 10.5px; line-height: 1.5; }
  .back-info .service-line { font-size: 14px; font-weight: 600; font-style: italic; margin-top: 4px; }
  .provide-rule { display: flex; align-items: center; gap: 8px; margin: 10px 0 12px; font-size: 10px; font-weight: 700; letter-spacing: 1px; }
  .provide-rule::before, .provide-rule::after { content: ""; flex: 1; height: 1px; background: var(--ink-cream); }
  .service-list { list-style: none; font-size: 11px; font-style: italic; line-height: 1.5; }
  .service-list li::before { content: "• "; }
  .service-list--right { position: absolute; top: 382px; right: 40px; text-align: right; }
  .service-list--right li::before { content: ""; }
  .service-list--right li::after { content: " •"; }
  .service-list--left { position: absolute; top: 462px; left: 28px; }
  .bottom-rule { position: absolute; top: 452px; left: 28px; width: 200px; height: 1px; background: var(--ink-cream); }

  /* front cover */
  .front { background: linear-gradient(160deg, var(--cream), var(--cream-deep)); }
  .front-name { position: absolute; top: 150px; left: 0; right: 0; text-align: center; }
  .front-name span { font-family: "Montserrat", sans-serif; font-weight: 600; font-size: 40px; line-height: 1.1; color: var(--red); letter-spacing: 1px; }
  .front-name i { display: block; width: 14px; height: 14px; margin: 14px auto 0; background: var(--orange); border-radius: 50%; }
  .front-wave { position: absolute; left: 0; bottom: 0; width: 405px; height: 160px; }
  .tagline { position: absolute; left: 30px; right: 30px; bottom: 36px; display: flex; align-items: center; gap: 8px; }
  .tagline::before, .tagline::after { content: ""; flex: 1; height: 1px; background: var(--orange-light); }
  .tagline span { background: var(--orange); color: var(--red-deep); font-size: 10.5px; font-weight: 600; padding: 4px 10px; border-radius: 2px; white-space: nowrap; }

  /* inside */
  .inside { background: linear-gradient(170deg, var(--cream), var(--cream-deep)); }
  .inside .faint-name { top: 150px; color: rgba(160,120,40,.13); }
  .pocket { position: absolute; left: 0; bottom: 0; width: 405px; height: 250px; }
  .pocket-text { position: absolute; color: var(--ink-cream); }
  .message { left: 30px; right: 40px; bottom: 48px; font-size: 10px; line-height: 1.55; color: var(--orange-light); }
  .contact { left: 0; right: 0; bottom: 70px; text-align: center; }
  .phone { display: flex; align-items: center; justify-content: center; gap: 8px; font-size: 22px; font-weight: 700; color: var(--ink-cream); }
  .phone::before, .phone::after { content: ""; width: 40px; height: 3px; border-top: 1px solid var(--ink-cream); border-bottom: 1px solid var(--ink-cream); }
  .thanks { margin-top: 10px; font-size: 14px; line-height: 1.4; color: var(--orange-light); }
</style>
</head>
<body>

<section class="spread spread--outside">
  <article class="panel back">
    <div class="faint-name">HARBEL<br>TRADEWORKS</div>
    <div class="back-info">
      <p>P.O. Box 418, Marlow Heights, NJ 07990</p>
      <p>www.HarbelTradeworks.com</p>
      <p class="service-line">A graphic that says 24-7 service</p>
      <div class="provide-rule">WE PROVIDE</div>
    </div>
    <ul class="service-list service-list--right">
      <li>Energy Audits</li>
      <li>1 Day Bathroom remodles</li>
      <li>Basement Waterproofing</li>
      <li>Garage Doors</li>
      <li>Home Theaters</li>
    </ul>
    <div class="bottom-rule"></div>
    <ul class="service-list service-list--left">
      <li>Solar</li>
      <li>Generators</li>
      <li>Home Security</li>
      <li>Home Automation</li>
      <li>Home Inspection</li>
    </ul>
  </article>

  <article class="panel front">
    <div class="front-name"><span>HARBEL<br>TRADEWORKS</span><i></i></div>
    <svg class="front-wave" viewBox="0 0 405 160" aria-hidden="true">
      <defs>
        <linearGradient id="bandRed" x1="0" y1="0" x2="1" y2="1">
          <stop offset="0" stop-color="#a3212a"/><stop offset="1" stop-color="#7e1419"/>
        </linearGradient>
      </defs>
      <path d="M0,40 C90,20 160,30 188,52 L202,66 L216,52 C244,30 315,20 405,8 V160 H0 Z" fill="url(#bandRed)"/>
      <path d="M0,40 C90,20 160,30 188,52 L202,66 L216,52 C244,30 315,20 405,8" fill="none" stroke="#e98a3c" stroke-width="4"/>
    </svg>
    <div class="tagline"><span>The Best Way To Live In New Jersey Is With Harbel"</span></div>
  </article>
</section>

<section class="spread spread--inside">
  <article class="panel inside">
    <div class="faint-name">HARBEL<br>TRADEWORKS</div>
    <svg class="pocket" viewBox="0 0 405 250" aria-hidden="true">
      <polygon points="0,0 405,70 405,250 0,250" fill="#9a1c22"/>
      <polygon points="0,0 405,70 405,74 0,4" fill="#7e1419"/>
    </svg>
    <p class="pocket-text message">Our name says it all, because for over 30 years we have prided ourselves on delivering the best service and exceeding our customers' expectations everyday. Whether you need something fixed, replaced or upgraded, no matter how large or small, the dedicated experts at Harbel Tradeworks are here to take care of you. Delivering the right solution for you the first time - everytime - and ensuring you are always 100% satisfied. If for any reason you want to speak with us, please do not hesitate to call or email. Thank you again for choosing Harbel Tradeworks.</p>
  </article>

  <article class="panel inside">
    <div class="faint-name">HARBEL<br>TRADEWORKS</div>
    <svg class="pocket" viewBox="0 0 405 250" aria-hidden="true">
      <polygon points="0,70 405,0 405,250 0,250" fill="#9a1c22"/>
      <polygon points="0,70 405,0 405,4 0,74" fill="#7e1419"/>
    </svg>
    <div class="pocket-text contact">
      <p class="phone">973-555-0148</p>
      <p class="thanks">We want to thank you for choosing<br>Harbel Tradeworks today</p>
    </div>
  </article>
</section>

</body>
</html>
```